Brochure for a website accessibility report

This brochure is related to a report that www.qelvantrix.org sell. The report shows the results of an automated audit of a websites accessibility. It shows details of issues found with screen shots, examples of code and provides remediation advice.

The brochure will be a pdf 8.5 inches by 11 inches. It can be anywhere from 6 to 10 pages.

The FlintVue™ name itself should be “Bree Serif” font. The fonts, styles, colors and sizes are up to you.

The images used and logo of the Office of Digital Reachworks and K7P logo are upload

We highlighted in blue page extracts from the report we sell. Do not use the blue highlight, it is merely there to show you where the specific examples of the report we sell are vs the other content in the report. The areas in blue which show the content from the actual report should be shown as an extract of the actual page of the report. You have flexibility to change the layout and the way the content look.

The red square callouts over the blue content are callouts that describe the specific page extracts. We used it as a red callout only so that you would be able to see it. You should change the specific location, look and feel of the callout to be appropriate

Target Market(s)

Marketing and Technical people

Industry/Entity Type

Information Technology

Font styles to use
Sans Serif

Colors

Designer to choose colors to be used in the design.

Requirements
Should not have
• wheelchairs, images of blind people

```html
<!DOCTYPE html>
<html lang="en">
<head>
<meta charset="utf-8">
<title>Report Page Extract – CSS Contrast Issue</title>
<link href="https://fonts.googleapis.com/css2?family=Roboto:wght@300;400;500;700&family=Roboto+Slab:wght@400&display=swap" rel="stylesheet">
<style>
  :root{
    --page:#ffffff;
    --navy:#0c3a5b;
    --ink:#ffffff;
    --green:#2bb673;
    --teal:#3cc8c0;
    --gold:#f5c518;
    --callout:#f6cd3c;
    --callout-ink:#0c3a5b;
    --alert:#e23c2a;
    --swatch-blue:#88c3d8;
    --swatch-grey:#eeeeee;
    --code-bg:#e7e7e7;
    --code-ink:#1d2b36;
  }
  *{box-sizing:border-box;margin:0;padding:0}
  html,body{width:928px;height:1200px;overflow:hidden;background:var(--page)}
  body{font-family:"Roboto",Arial,sans-serif;color:var(--ink)}
  .stage{position:relative;width:1046px;height:1350px;transform:scale(0.8872);transform-origin:0 0}
  .report-page{position:absolute;left:60px;top:57px;width:925px;height:1233px;background:var(--navy);border-radius:56px;box-shadow:0 4px 14px rgba(0,0,0,.12)}
  .abs{position:absolute}
  .section-title{left:116px;top:86px;font-size:34px;font-weight:700;color:var(--green)}
  .body-text{font-size:18px;font-weight:300;line-height:22.5px;text-align:justify;width:810px}
  .intro{left:116px;top:152px}
  .bullet{position:absolute;width:774px}
  .bullet::before{content:"";position:absolute;left:-32px;top:8px;width:7px;height:7px;background:var(--teal)}
  .sub-bullet{position:absolute;width:722px}
  .sub-bullet::before{content:"";position:absolute;left:-51px;top:8px;width:8px;height:8px;border-radius:50%;background:var(--teal)}
  b,strong{font-weight:500}
  .issue-head{left:110px;top:480px;display:flex;align-items:center;gap:8px;font-size:18px;font-weight:500}
  .issue-head .label-gold{color:var(--gold)}
  .gold{color:var(--gold)}
  .sub-head{font-size:18px;font-weight:500}
  .links{left:173px;top:926px;font-size:18px;line-height:22.5px;color:var(--teal);font-weight:400}
  .example{left:118px;top:1027px;font-size:18px;letter-spacing:.3px}
  .example b{font-weight:700}
  .swatch{position:absolute;width:76px;height:76px;box-shadow:0 2px 6px rgba(0,0,0,.35)}
  .swatch-label{position:absolute;font-size:18px;line-height:26px}
  .swatch-label .name{font-weight:500}
  .swatch-label .val{padding-left:28px;font-weight:300}
  .issues-head{left:473px;top:1076px;font-size:15px;font-weight:700}
  .issues-text{left:473px;top:1103px;width:453px;font-size:15px;font-weight:300;line-height:21px;text-align:justify}
  .code-head{left:472px;top:1176px;font-size:18px;font-weight:500}
  .code-box{left:470px;top:1209px;width:270px;height:28px;background:var(--code-bg);color:var(--code-ink);font-family:"Roboto Slab",Georgia,serif;font-size:14px;line-height:28px;padding-left:15px}
  .callout-shape{position:absolute;left:0;top:0}
  .callout-text{position:absolute;color:var(--callout-ink);font-size:16px;line-height:20.5px;font-weight:400}
</style>
</head>
<body>
<div class="stage">
  <div class="report-page"></div>

  <h1 class="abs section-title">CSS</h1>

  <p class="abs body-text intro">Pages that use stylesheets (CSS) should be checked to make sure they're still readable and well organized without stylesheet(s).</p>

  <p class="bullet body-text" style="left:152px;top:214px;width:774px">One way to check this would be to momentarily rename the StyleSheet, and make sure pages referencing it are still readable.</p>
  <p class="bullet body-text" style="left:152px;top:272px;width:774px">If renaming a Stylesheet is not possible (e.g. on live systems) then you can disable StyleSheets using your Web browsers built in tools or plugins as follows.</p>

  <p class="sub-bullet body-text" style="left:203px;top:332px">Foxglade (Select Tools menu at the top of the Foxglade browser window, then select Web <b>Developer</b> &gt; <b>Style Editor</b>)</p>
  <p class="sub-bullet body-text" style="left:203px;top:388px">Netwave Explorer (<b>Press F12</b> for Web Developer Tools when in an NE browser window) Chromalux (Select the Chromalux menu at the top-right of the Chromalux browser window, then select <b>Tools</b> &gt; <b>Developer tools</b>)</p>

  <div class="abs issue-head">
    <svg width="28" height="25" viewBox="0 0 28 25" aria-hidden="true"><path d="M14 2 L26 23 H2 Z" fill="none" stroke="var(--alert)" stroke-width="2.4" stroke-linejoin="round"/><rect x="12.8" y="8.5" width="2.4" height="8" fill="var(--alert)"/><rect x="12.8" y="18.3" width="2.4" height="2.4" fill="var(--alert)"/></svg>
    <span>ISSUE: <span class="label-gold">CONTRAST MINIMUM (PRIORITY 1)</span></span>
  </div>

  <p class="abs body-text" style="left:116px;top:512px">The visual presentation of text must have a contrast ratio of at least 4.5:1 for normal sized text and at least 3:1 for large sized text (24px+ or 18.5px+ and emboldened).</p>
  <p class="abs body-text" style="left:116px;top:563px">Provide enough luminous color contrast between text and its background so that it can be read by people with moderately low vision (who do not use contrast-enhancing assistive technology). The minimum contrast success criterion (1.4.3) applies to text in the page, including placeholder text and text that is shown when a pointer is hovering over an object or when an object has keyboard focus. If any of these are used in a page, the text needs to provide sufficient contrast. Text that is decorative and conveys no information is excluded.</p>
  <p class="abs body-text" style="left:116px;top:704px">Issue is relevant to checkpoints: &nbsp;&nbsp;&nbsp;<span class="gold">1.4.3 (AA)</span>.</p>

  <h2 class="abs sub-head" style="left:116px;top:754px">General Remediation Advice:</h2>
  <p class="abs body-text" style="left:116px;top:783px">Increase the contrast ratio and/or the font sizing and/or positioning accordingly such that the visual luminous contrast ratio between the foreground text color and the multiplied background color meet or exceed the described ratios. Alternatively, provide a user option to switch to a view utilizing sufficiently higher contrast values.</p>

  <h2 class="abs sub-head" style="left:116px;top:903px">Suggested Reading:</h2>
  <div class="abs links">Distinguishible<br>Contrast (Minimum)<br>Shadecheck.net</div>

  <p class="abs example"><b>EXAMPLE 1 OF 23:</b> &nbsp;HTTP://WWW.NORTHMERE.ORG/EN/NEWTECHNOLOGIES/</p>

  <div class="swatch" style="left:117px;top:1079px;background:var(--swatch-blue)"></div>
  <div class="swatch-label" style="left:229px;top:1074px"><div class="name">Background Color</div><div class="val">rgb(136,195,216)</div><div class="val">#88c3d8</div></div>
  <div class="swatch" style="left:117px;top:1171px;background:var(--swatch-grey)"></div>
  <div class="swatch-label" style="left:229px;top:1165px"><div class="name">Background Color</div><div class="val">rgb(238,238,238)</div><div class="val">#eeeeee</div></div>

  <h3 class="abs issues-head">SPECIFIC ISSUES:</h3>
  <p class="abs issues-text">The text '<b style="font-weight:700">Northmere Secretariat staff</b>' over the background has a contrast ratio of 1.66:1 while the required ratio is 4.5:1. Increase the contrast ratio by at least 171.08% to pass.</p>

  <h3 class="abs code-head">CODE SNIPPET</h3>
  <div class="abs code-box">&lt;h5&gt;Northmere Secretariat staff&lt;/h5&gt;</div>

  <svg class="callout-shape" width="1046" height="1350" aria-hidden="true">
    <path d="M417 898 H840 Q860 898 860 918 V986 Q860 1006 840 1006 H440 L397 1050 V918 Q397 898 417 898 Z" fill="var(--callout)"/>
    <path d="M473 1250 H820 L860 1185 V1315 Q860 1335 840 1335 H473 Q453 1335 453 1315 V1270 Q453 1250 473 1250 Z" fill="var(--callout)"/>
  </svg>
  <p class="callout-text" style="left:433px;top:932px;width:400px">Color contrast failures show the color combinations tested with their corresponding RGB and HEX code</p>
  <p class="callout-text" style="left:475px;top:1275px;width:360px;text-align:justify">The text with the issue is detailed and shows the specific amount of contract required to pass</p>
</div>
</body>
</html>
```